Grey Fennel Medical Website to make connecting and communicating easier

To create a unique, user-friendly, professional website for patients and professionals to access education/ information, forms, appointments, contact details, and data about us, and for us to have the capacity to link to various cloud-based platforms.
To use the logo design and colour scheme we have just sourced.

WEBSITE to be eye catching, Inspiring and alluring
- efficient and logical
- professional and trustworthy appearance
- health focus "living health matters"
- user friendly
- ability to link with cloud-based software and video conferencing tools/ telehealth
- colours- black/ white teal and ?silver

PAGES:
page 1 - Our clinic and staff, services offered, contact us- address/ map / contact details- social media connections
page 2- patients and visitors - New patient forms to complete, news and patient informtion (educatinal)
page 3 - health professionals -referral forms, research and education
page 3- online appointments
page 4 - Quick links - partners, other services
page 5- privacy policy, disclaimer

HI, Could we please extend the deadline another 5 days, so sorry just struggling with my workload to be able to keep up and I am wanting to liaise more with the designer that I will choose. I am so happy with SketchHarbor and all the designers - thank you! Thank you so much!!

Target Market(s)

Patients - mostly over 60's so the website must be minimal clicks and simple to navigate
Professionals - for education and access forms

Industry/Entity Type

Health Care

Coding

Coded - Design and coding required

Number of Pages Required

5+ page

Font styles to use
Sans Serif
Script

Colors
33b8a4
86cfc6

Requirements
Must have
• WEBSITE to be eye catching, Inspiring and alluring
- efficient and logical
- user friendly

WEBSITE - professional and user friendly
- ability to link with cloud based software and videoconferencing/ telehealth
Nice to have
• clean and crisp presentation
happy for an innovative look
room to add more services and ability to link pages and resources
Should not have
• Please ensure the website is not:
clunky
difficult to navigate
common and cheap looking

```html
<!DOCTYPE html>
<html lang="en">
<head>
<meta charset="utf-8">
<title>Grey Fennel Medical – Patients and Visitors</title>
<link rel="stylesheet" href="https://fonts.googleapis.com/css2?family=Montserrat:wght@500;600;700&family=Mulish:wght@400;600;700&display=swap">
<style>
  :root {
    --teal: #33b8a4;
    --teal-dark: #1f8a78;
    --teal-soft: #86cfc6;
    --ink: #1d2b2a;
    --text: #555a5a;
    --light: #f5f5f5;
    --white: #ffffff;
  }
  * { margin: 0; padding: 0; box-sizing: border-box; }
  html, body { width: 1200px; height: 1200px; overflow: hidden; background: var(--white); }
  body { position: relative; font-family: "Mulish", sans-serif; color: var(--text); }
  .abs { position: absolute; }

  .topbar { left: 314px; top: 0; width: 572px; height: 52px; background: var(--light); }
  .brand { font-family: "Mulish", sans-serif; font-weight: 700; color: var(--teal); font-size: 10px; display: flex; align-items: center; gap: 5px; white-space: nowrap; }
  .brand .dot { width: 12px; height: 12px; border-radius: 50%; background: var(--teal); }
  .contact-mini { font-size: 6.3px; color: var(--ink); display: flex; align-items: center; gap: 4px; white-space: nowrap; }

  .nav { top: 65px; font-family: "Montserrat", sans-serif; font-size: 7.2px; font-weight: 500; color: var(--ink); white-space: nowrap; }
  .nav.active { color: var(--teal); }

  .hero-photo { left: 314px; top: 87px; width: 572px; height: 134px; background: linear-gradient(90deg, #e4e9f1 0%, #d7deea 45%, #b9c8dc 70%, #9fd8d4 100%); }
  .hero-title { left: 391px; top: 130px; font-family: "Montserrat", sans-serif; font-weight: 700; font-size: 22px; line-height: 22px; color: var(--ink); }
  .hero-title span { color: var(--teal-dark); display: block; }

  .section-title { font-family: "Montserrat", sans-serif; font-weight: 600; font-size: 19px; color: var(--ink); width: 572px; left: 314px; text-align: center; }
  .rule { height: 2px; width: 31px; background: var(--teal-dark); }
  .copy { font-size: 7.2px; line-height: 10.7px; }
  .copy.lead { color: var(--teal-dark); }
  .btn { background: var(--teal); color: var(--white); border-radius: 12px; font-weight: 700; font-size: 6.3px; letter-spacing: 0.5px; display: flex; align-items: center; justify-content: center; box-shadow: 0 1px 2px rgba(0,0,0,0.15); }

  .band { left: 314px; top: 404px; width: 290px; height: 268px; background: var(--teal); color: var(--white); }
  .band-photo { left: 604px; top: 404px; width: 282px; height: 268px; background: linear-gradient(160deg, #e9f1f6 0%, #c9dcea 40%, #2a5fb8 60%, #dfe8ef 85%); }
  .band h3 { position: absolute; font-family: "Montserrat", sans-serif; font-weight: 600; font-size: 11px; left: 35px; white-space: nowrap; }
  .band p { position: absolute; left: 35px; width: 236px; font-size: 7.2px; line-height: 10.7px; }
  .band ul { position: absolute; top: 101px; list-style: disc; font-size: 7.2px; line-height: 10.7px; padding-left: 10px; white-space: nowrap; }

  .doctor-photo { left: 352px; top: 768px; width: 198px; height: 204px; border-radius: 5px; background: linear-gradient(135deg, #cfe8f5 0%, #a9d3ec 50%, #e8f2f7 100%); }

  .footer { left: 314px; top: 1012px; width: 572px; height: 185px; background: var(--light); }
  .f-head { font-family: "Montserrat", sans-serif; font-weight: 500; font-size: 7.2px; color: var(--ink); }
  .f-item { font-size: 6.2px; color: var(--ink); white-space: nowrap; }
  .f-line { left: 352px; top: 1163px; width: 496px; height: 1px; background: #cfcfcf; }
  .copyright { left: 314px; top: 1175px; width: 572px; text-align: center; font-size: 5.3px; color: var(--ink); }
  .copyright a { color: var(--teal); text-decoration: underline; }
</style>
</head>
<body>
  <div class="abs topbar"></div>
  <div class="abs brand" style="left:352px; top:19px;"><span class="dot"></span>Grey Fennel Medical</div>
  <div class="abs contact-mini" style="left:697px; top:22px;">
    <svg width="9" height="7" viewBox="0 0 9 7"><rect x="0.5" y="0.5" width="8" height="6" fill="none" stroke="#33b8a4" stroke-width="0.8"/><path d="M0.5 0.7 L4.5 4 L8.5 0.7" fill="none" stroke="#33b8a4" stroke-width="0.8"/></svg>
    info@gfmedical.test
  </div>
  <div class="abs contact-mini" style="left:784px; top:21px;">
    <svg width="8" height="8" viewBox="0 0 8 8"><path d="M1.5 0.8 L3 2.6 L2.2 3.5 Q3 5.2 4.6 5.9 L5.5 5 L7.3 6.5 L6.4 7.4 Q2 6.8 0.6 1.7 Z" fill="none" stroke="#33b8a4" stroke-width="0.7"/></svg>
    (800) 555-0142
  </div>

  <nav>
    <div class="abs nav active" style="left:352px;">HOME</div>
    <div class="abs nav" style="left:395px;">ABOUT US</div>
    <div class="abs nav" style="left:453px;">OUR SERVICES</div>
    <div class="abs nav" style="left:527px;">PATIENTS &amp; VISITORS</div>
    <div class="abs nav" style="left:622px;">APPOINTMENTS</div>
    <div class="abs nav" style="left:700px;">NEWS &amp; INFORMATION</div>
    <div class="abs nav" style="left:801px;">CONTACT US</div>
  </nav>

  <div class="abs hero-photo" role="img" aria-label="Photo of a smiling nurse comforting an elderly patient"></div>
  <h1 class="abs hero-title">Patients<span>and Visitors</span></h1>

  <h2 class="abs section-title" style="top:252px;">New Patients</h2>
  <div class="abs rule" style="left:537px; top:278px;"></div>
  <p class="abs copy lead" style="left:479px; top:293px; width:240px;">When you make your first appointment, please come in early to fill out information forms.</p>
  <p class="abs copy" style="left:479px; top:325px; width:236px;">If that is not convenient, we encourage you to print out the following forms and fill them in at your leisure. Bring them in with you on your appointment.</p>
  <div class="abs btn" style="left:547px; top:371px; width:105px; height:20px;">New Patient Forms</div>

  <section class="abs band">
    <h3 style="top:26px;">Insurance Plan Information</h3>
    <p style="top:44px;">Each patient is responsible for knowing his or her plan’s benefit package, co-payment, deductible, non-covered services and restrictions. Many plans have participating or preferred providers. We participate in most area health plans. The following are some of the plans that we accept.</p>
    <ul style="left:35px;">
      <li>Quillmoor (PPO, POS)</li>
      <li>Brambleton Mutual</li>
      <li>Pellwick</li>
      <li>Fernhollow</li>
      <li>Saltmeadow Cover</li>
    </ul>
    <ul style="left:139px;">
      <li>Dunmere Vale</li>
      <li>Ashgrove</li>
      <li>Starlow</li>
      <li>Corrinbay</li>
      <li>Hollinsby</li>
    </ul>
    <h3 style="top:172px;">Out Of Plan Patients</h3>
    <p style="top:190px;">Lorem ipsum dolor sit amet, consetetur sadipscing elitr, sed diam nonumy eirmod tempor invidunt ut labore et dolore magna aliquyam erat, sed diam voluptua. At vero eos et accusam et justo duo dolores et ea rebum. Stet clita kasd gubergren, no sea takimata sanctus est.</p>
  </section>
  <div class="abs band-photo" role="img" aria-label="Photo of health insurance cards lying beside a stethoscope on a lab report"></div>

  <h2 class="abs section-title" style="top:712px;">Referrals</h2>
  <div class="abs rule" style="left:558px; top:737px;"></div>
  <div class="abs doctor-photo" role="img" aria-label="Photo of a smiling doctor holding folders"></div>
  <p class="abs copy lead" style="left:599px; top:808px; width:236px;">But I must explain to you how all this mistaken idea of denouncing pleasure and praising pain was born and I will give you a complete</p>
  <p class="abs copy" style="left:599px; top:840px; width:236px;">Account of the system, and expound the actual teachings of the great explorer of the truth, the master-builder of human happiness. No one rejects, dislikes, or avoids pleasure itself, because it is pleasure, but because those who do not know how to pursue pleasure rationally encounter consequences that are extremely painful. Nor again is there anyone who loves or pursues or desires to obtain pain of itself.</p>
  <div class="abs btn" style="left:599px; top:917px; width:107px; height:20px;">Referral Forms</div>

  <footer class="abs footer"></footer>
  <div class="abs brand" style="left:352px; top:1054px;"><span class="dot"></span>Grey Fennel Medical</div>

  <div class="abs f-head" style="left:507px; top:1038px;">CONTACT</div>
  <svg class="abs" style="left:497px; top:1061px;" width="7" height="10" viewBox="0 0 7 10"><path d="M3.5 9.5 Q0.5 5.5 0.5 3.5 A3 3 0 0 1 6.5 3.5 Q6.5 5.5 3.5 9.5 Z" fill="none" stroke="#33b8a4" stroke-width="0.7"/><circle cx="3.5" cy="3.5" r="1" fill="none" stroke="#33b8a4" stroke-width="0.6"/></svg>
  <div class="abs f-item" style="left:507px; top:1061px; line-height:10.5px;">48 Fennel Lane<br>Maple Grove, AZ 85099</div>
  <svg class="abs" style="left:496px; top:1093px;" width="9" height="7" viewBox="0 0 9 7"><rect x="0.5" y="0.5" width="8" height="6" fill="none" stroke="#33b8a4" stroke-width="0.8"/><path d="M0.5 0.7 L4.5 4 L8.5 0.7" fill="none" stroke="#33b8a4" stroke-width="0.8"/></svg>
  <div class="abs f-item" style="left:507px; top:1092px;">care@gfmedical.test</div>
  <svg class="abs" style="left:497px; top:1114px;" width="8" height="8" viewBox="0 0 8 8"><path d="M1.5 0.8 L3 2.6 L2.2 3.5 Q3 5.2 4.6 5.9 L5.5 5 L7.3 6.5 L6.4 7.4 Q2 6.8 0.6 1.7 Z" fill="none" stroke="#33b8a4" stroke-width="0.7"/></svg>
  <div class="abs f-item" style="left:507px; top:1114px;">(345) 555-0178</div>

  <div class="abs f-head" style="left:669px; top:1038px;">MENU</div>
  <div class="abs f-item" style="left:671px; top:1062px;">About Us</div>
  <div class="abs f-item" style="left:671px; top:1077px;">Our Services</div>
  <div class="abs f-item" style="left:671px; top:1092px;">Patients &amp; Visitors</div>
  <div class="abs f-item" style="left:671px; top:1108px;">Appointments</div>
  <div class="abs f-item" style="left:671px; top:1123px;">News &amp; Information</div>
  <div class="abs f-item" style="left:671px; top:1139px;">Contact Us</div>

  <div class="abs f-head" style="left:804px; top:1039px;">FOLLOW US</div>
  <div class="abs f-item" style="left:804px; top:1061px;">Chatterbook</div>
  <div class="abs f-item" style="left:804px; top:1076px;">Chirpline</div>
  <div class="abs f-item" style="left:804px; top:1091px;">Snapgram</div>
  <div class="abs f-item" style="left:804px; top:1107px;">Circlesphere</div>
  <div class="abs f-item" style="left:804px; top:1122px;">Streamtube</div>

  <div class="abs f-line"></div>
  <div class="abs copyright">©2020 Grey Fennel Medical. All Rights Reserved. &nbsp; <a>Disclaimer</a> | <a>Privacy Policy</a></div>
</body>
</html>
```